Kelvor Engineers: Why you should hire us keepsake

New design. Open to plastic cards. We are an engineering firm that designs cell phone towers and commercial buildings. Please check out our website www.kelvorstruct.com for more details. We want people to remember our card and for it to be useful if possible. We want the same look and feel on these cards to be translated to other marketing material we may need such as brochures.

Target Market(s)

Architects, Developers and Telecommunication Carriers

Industry/Entity Type

Engineering

Contact Information for Business Card

Card with our company colors, logo, and innovative design with elements related to our industry.

Font styles to use
Sans Serif

Colors
9bcb3c
abd036
0255a3

Requirements
Must have
• Sleek and hip design
Nice to have
• Bright lime green and navy coloring that pops with an innovative design.
Should not have
• A basic and boring design

```html
<!DOCTYPE html>
<html lang="en">
<head>
<meta charset="UTF-8">
<title>Kelvor Engineers — Business Card</title>
<link rel="stylesheet" href="https://fonts.googleapis.com/css2?family=Open+Sans:wght@400;600;800&display=swap">
<style>
  :root {
    --stage: #3a3430;
    --navy: #02305f;
    --black: #0c0c0c;
    --lime: #22f22a;
    --ink-light: #e6ecf4;
    --divider: rgba(255,255,255,0.35);
  }
  * { box-sizing: border-box; margin: 0; padding: 0; }
  html, body {
    width: 1200px; height: 844px; overflow: hidden;
    background: var(--stage);
    font-family: "Open Sans", Arial, sans-serif;
  }
  .stage {
    position: relative; width: 1200px; height: 844px;
    display: flex; align-items: center; justify-content: center; gap: 60px;
  }
  .card {
    position: relative; width: 520px; height: 300px;
    box-shadow: 0 14px 30px rgba(0,0,0,0.45);
  }
  .card--front { background: var(--navy); }
  .card--back { background: var(--black); }

  .brand-name {
    color: var(--lime); font-weight: 800; letter-spacing: -0.5px;
    line-height: 1; white-space: nowrap;
  }
  .card--front .brand-name {
    position: absolute; left: 34px; top: 132px; font-size: 30px;
  }
  .card--front .brand-name .word { display: block; }

  .divider {
    position: absolute; left: 268px; top: 40px; width: 1px; height: 220px;
    background: linear-gradient(var(--divider), rgba(255,255,255,0));
  }
  .contact {
    position: absolute; left: 292px; top: 66px; right: 16px;
  }
  .contact__name {
    color: var(--lime); font-size: 16px; font-weight: 400;
    letter-spacing: 0.3px; text-transform: uppercase; margin-bottom: 30px;
  }
  .contact__list { list-style: none; }
  .contact__item {
    display: flex; align-items: center; gap: 8px;
    color: var(--ink-light); font-size: 13px; line-height: 18px;
  }
  .contact__item svg { width: 10px; height: 10px; flex: none; fill: var(--lime); }

  .card--back .brand-name {
    position: absolute; left: 0; right: 0; top: 110px;
    text-align: center; font-size: 40px;
  }
  .tagline {
    position: absolute; left: 0; right: 0; top: 206px; text-align: center;
    color: var(--lime); font-size: 11px; letter-spacing: 0.4px;
  }
</style>
</head>
<body>
<main class="stage">
  <section class="card card--front" aria-label="Business card front">
    <div class="brand-name"><span class="word">Kelvor</span><span class="word">Engineers</span></div>
    <div class="divider"></div>
    <div class="contact">
      <h1 class="contact__name">Dana Whitlock Reyes</h1>
      <ul class="contact__list">
        <li class="contact__item">
          <svg viewBox="0 0 10 10" aria-hidden="true"><path d="M1 2.5C1 1.7 1.7 1 2.5 1h5C8.3 1 9 1.7 9 2.5V4H7V3H3v1H1z M2 5h6l1 4H1z"/></svg>
          555.014.2231
        </li>
        <li class="contact__item">
          <svg viewBox="0 0 10 10" aria-hidden="true"><path d="M3 0h4a1 1 0 0 1 1 1v8a1 1 0 0 1-1 1H3a1 1 0 0 1-1-1V1a1 1 0 0 1 1-1zm0 1.5v6h4v-6z"/></svg>
          555.018.4472
        </li>
        <li class="contact__item">
          <svg viewBox="0 0 10 10" aria-hidden="true"><path d="M0 2h10v6H0zm1 1 4 3 4-3z"/></svg>
          DREYES@kelvorstruct.com
        </li>
        <li class="contact__item">
          <svg viewBox="0 0 10 10" aria-hidden="true"><circle cx="5" cy="5" r="5"/></svg>
          www.kelvorstruct.com
        </li>
      </ul>
    </div>
  </section>

  <section class="card card--back" aria-label="Business card back">
    <div class="brand-name">Kelvor Engineers</div>
    <p class="tagline">MULTI-DISPLINE ENGINEERING</p>
  </section>
</main>
</body>
</html>
```